Youth Lifting Youth Business Card. We have existing logo

We need a business card design from an existing logo.
Our logo is in black and white but would love to add in the color burgundy but we're open to any color. Our website is www.youthliftingyouthmv.org

Target Market(s)

corporations and foundations who will be donating

Industry/Entity Type

Business

Contact Information for Business Card

Address: 2318 Marwick Ave Calder Bay, CA 95721
Name: Corin Halvorsen
Founder email: corin.halvorsen@youthliftingyouthmv.org
Phone: 805-637-9081

Requirements
Nice to have
• Our colors are burgundy and white, but that's not a necessity

```html
<!DOCTYPE html>
<html lang="en">
<head>
<meta charset="utf-8">
<title>Youth Lifting Youth – Business Card</title>
<link rel="stylesheet" href="https://fonts.googleapis.com/css2?family=Tinos:wght@400;700&display=swap">
<style>
  :root {
    --backdrop: #e9e9e7;
    --card: #ffffff;
    --ink: #000000;
    --rail: #a6a6a6;
  }
  html, body {
    margin: 0;
    width: 1200px;
    height: 902px;
    overflow: hidden;
    background: var(--backdrop);
  }
  .card {
    position: absolute;
    left: 100px;
    top: 165px;
    width: 1000px;
    height: 572px;
    background: var(--card);
    font-family: "Tinos", "Times New Roman", serif;
    color: var(--ink);
    box-shadow: 0 6px 24px rgba(0,0,0,0.18);
    overflow: hidden;
  }
  .rail {
    position: absolute;
    top: 0;
    width: 53px;
    height: 100%;
    background: var(--rail);
  }
  .rail--left { left: 0; }
  .rail--right { right: 0; }
  .gap { position: absolute; background: var(--card); }
  .bar { position: absolute; background: var(--ink); }
  .gap--band { left: 0; width: 1000px; top: 280px; height: 76px; }
  .bar--left { left: 0; width: 53px; top: 286px; height: 64px; }
  .bar--main { left: 438px; width: 562px; top: 286px; height: 64px; }
  .gap--tab { left: 947px; width: 53px; top: 96px; height: 63px; }
  .bar--tab { left: 947px; width: 53px; top: 103px; height: 49px; }

  .holder {
    position: absolute;
    right: 76px;
    top: 96px;
    text-align: right;
  }
  .holder__name {
    margin: 0;
    font-size: 42px;
    font-weight: 700;
    line-height: 1;
    letter-spacing: 0.5px;
  }
  .holder__role {
    margin: 4px 0 0;
    font-size: 22px;
    line-height: 1;
  }

  .brand {
    position: absolute;
    left: 125px;
    top: 198px;
    width: 244px;
    height: 244px;
    border: 3px solid var(--ink);
    border-radius: 50%;
    box-sizing: border-box;
    display: flex;
    align-items: center;
    justify-content: center;
    text-align: center;
  }
  .brand__name {
    font-size: 26px;
    line-height: 1.2;
    font-weight: 400;
    padding: 0 30px;
  }

  .contact {
    position: absolute;
    right: 76px;
    top: 384px;
    margin: 0;
    padding: 0;
    list-style: none;
    font-size: 22px;
  }
  .contact__item {
    display: flex;
    justify-content: flex-end;
    align-items: flex-start;
    gap: 28px;
    line-height: 28px;
    margin-bottom: 8px;
    text-align: right;
  }
  .contact__icon {
    width: 18px;
    height: 18px;
    margin-top: 5px;
    flex: none;
    fill: var(--ink);
  }
</style>
</head>
<body>
  <article class="card">
    <div class="rail rail--left"></div>
    <div class="rail rail--right"></div>
    <div class="gap gap--band"></div>
    <div class="bar bar--left"></div>
    <div class="bar bar--main"></div>
    <div class="gap gap--tab"></div>
    <div class="bar bar--tab"></div>

    <div class="holder">
      <h1 class="holder__name">Corin Halvorsen</h1>
      <p class="holder__role">Founder</p>
    </div>

    <div class="brand">
      <span class="brand__name">Youth Lifting Youth</span>
    </div>

    <ul class="contact">
      <li class="contact__item">
        <span>555-637-9081</span>
        <svg class="contact__icon" viewBox="0 0 24 24" aria-hidden="true"><path d="M6.6 10.8a15.2 15.2 0 0 0 6.6 6.6l2.2-2.2a1 1 0 0 1 1-.25 11.4 11.4 0 0 0 3.6.57 1 1 0 0 1 1 1V20a1 1 0 0 1-1 1A17 17 0 0 1 3 4a1 1 0 0 1 1-1h3.5a1 1 0 0 1 1 1c0 1.25.2 2.45.57 3.6a1 1 0 0 1-.25 1z"/></svg>
      </li>
      <li class="contact__item">
        <span>corin.halvorsen@youthliftingyouthmv.org</span>
        <svg class="contact__icon" viewBox="0 0 24 24" aria-hidden="true"><path d="M2 5h20v14H2z"/><path d="M3 6h18l-9 6.5z" fill="#fff"/></svg>
      </li>
      <li class="contact__item">
        <span>2318 Marwick Ave Calder Bay,<br>CA 95721</span>
        <svg class="contact__icon" viewBox="0 0 24 24" aria-hidden="true"><path d="M12 1a7 7 0 0 0-7 7c0 5.2 7 15 7 15s7-9.8 7-15a7 7 0 0 0-7-7zm0 9.5A2.5 2.5 0 1 1 12 5.5a2.5 2.5 0 0 1 0 5z"/></svg>
      </li>
    </ul>
  </article>
</body>
</html>
```